Poster for Folk High School in Norway

Hi! I want to create a poster for our International course. I represent Folkehøgskolen Vestbrekka (www.fhvbrekka.no), and we would like to create posters to send around to different places to recruit youth to come to our school. The target gruoup is people in the age between 18-20 years.
Please check our website for inspiration regarding poster-design.
Keywords for design: Fresh, warm, joyfull, eyecatcher.
A goal would be to create a feeling that joining this school will give me great experiences, and I also will be a part of a larger community.
At the end of the project, I would like access to the project-file. (I assume a program in the Adobe-series will be used). This because I would like to have the opurtunity to change the text... The other layers might be merged, or whatever... :)
Regarding files, I have a PSD file for the photostudio pictures. In this file, the background is removed. Let me know if you want me to send this file. Maybe it will save you some time... :) If needed, for some pictures I also have the RAW-format.
The size of the poster: About A2 size. 600 dpi(?)
The logo must be a part of the poster.
You'll find the text among the uploaded files.
And of course: You choose how many pictures that you want to use...
Updates
There has been a change in text for the poster. Originally, it was to much: The new text:Headline:Norway + Folk High School = A good matchInterested in doing something quite different next year?Info on poster:- Learn the Norwegian language and culture- Live close, socialize and be a part of a Norwegian boarding school.- Idyllically located in beautifully natural surroundings in a small town south in Norway. Take a chance, this could easily be a perfect year for you!For more information: www.fhssorlandet.nopost@fhssorlandet.no+47 38 27 11 00 Added Thursday, June 25, 2015

```html
<!DOCTYPE html>
<html lang="en">
<head>
<meta charset="utf-8">
<title>Folkehøgskolen Vestbrekka – International Course Poster</title>
<link rel="stylesheet" href="https://fonts.googleapis.com/css2?family=Oswald:wght@300;400;500;600&display=swap">
<style>
  :root {
    --pink: #e4356b;
    --pink-dark: #d42b5e;
    --teal: #3fc1c7;
    --teal-light: #8fdce0;
    --teal-pale: #c3ecee;
    --teal-deep: #3a8e93;
    --paper: #ffffff;
  }
  * { margin: 0; padding: 0; box-sizing: border-box; }
  html, body { width: 839px; height: 1200px; overflow: hidden; background: var(--paper); }
  .poster {
    position: relative;
    width: 839px; height: 1200px;
    background: var(--paper);
    font-family: "Oswald", "Arial Narrow", sans-serif;
    text-transform: uppercase;
    overflow: hidden;
  }
  .decor { position: absolute; left: 0; top: 0; width: 839px; height: 1200px; }

  .headline-bar {
    position: absolute; color: var(--paper); white-space: nowrap;
    font-weight: 300; font-size: 38px; letter-spacing: 1px;
    display: flex; align-items: center; padding-left: 22px;
  }
  .headline-bar strong { font-weight: 600; margin-left: 10px; }
  .headline-bar--first { left: 56px; top: 50px; width: 594px; height: 84px; background: var(--pink-dark); }
  .headline-bar--second { left: 358px; top: 134px; width: 436px; height: 68px; background: var(--pink); }
  .headline-bar--second strong { margin-left: 0; margin-right: 10px; }

  .photo { position: absolute; }
  .photo--students { left: 0; top: 224px; width: 420px; height: 266px; background: linear-gradient(135deg, #d8d8d8 0%, #9a9a9a 45%, #4b4b4b 100%); }
  .photo--group { left: 322px; top: 490px; width: 517px; height: 223px; background: linear-gradient(180deg, #e9e9e9 0%, #bdbdbd 55%, #6d6d6d 100%); }
  .photo--canoe { left: 0; top: 740px; width: 460px; height: 197px; background: linear-gradient(160deg, #cfd6d4 0%, #8f9a98 50%, #4f5a58 100%); }

  .match {
    position: absolute; left: 330px; top: 226px; width: 230px;
    color: var(--paper); font-weight: 400; white-space: nowrap; line-height: 1.1;
  }
  .match .big { display: block; font-size: 36px; }
  .match .small { display: block; font-size: 23px; font-weight: 500; }

  .feature {
    position: absolute; font-weight: 300; font-size: 21px; line-height: 1.15;
    letter-spacing: 0.5px; white-space: nowrap;
  }
  .feature--language { left: 565px; top: 410px; color: var(--teal-deep); }
  .feature--living { left: 84px; top: 500px; color: var(--teal); text-align: center; }
  .feature--location { left: 503px; top: 727px; color: var(--teal); }

  .closing {
    position: absolute; left: 50px; top: 1015px; width: 495px; height: 118px;
    background: var(--pink); color: var(--paper);
    padding: 14px 18px; font-size: 31px; font-weight: 300; line-height: 1.35;
    letter-spacing: 0.5px; white-space: nowrap;
  }
  .closing strong { font-weight: 600; }

  .contact {
    position: absolute; left: 52px; top: 1150px; width: 640px;
    display: flex; justify-content: space-between;
    color: var(--pink); font-size: 17px; font-weight: 400; letter-spacing: 0.5px;
  }

  .school-mark {
    position: absolute; left: 695px; top: 1035px; width: 125px;
    display: flex; flex-direction: column; align-items: center; gap: 8px;
    color: var(--pink); font-weight: 400; font-size: 14px; line-height: 1.05; text-align: center;
  }
  .school-mark .square { width: 54px; height: 54px; background: var(--pink); }
</style>
</head>
<body>
<div class="poster">

  <div class="photo photo--students" role="img" aria-label="Black and white photo of students working together at a table"></div>
  <div class="photo photo--group" role="img" aria-label="Black and white photo of a group of students jumping outdoors"></div>
  <div class="photo photo--canoe" role="img" aria-label="Photo of students paddling a canoe on a lake"></div>

  <svg class="decor" viewBox="0 0 839 1200" aria-hidden="true">
    <polygon points="320,205 640,205 520,500" fill="var(--teal)" opacity="0.92"/>
    <polygon points="560,205 760,205 700,330" fill="var(--teal-light)" opacity="0.8"/>
    <polygon points="0,470 70,515 0,560" fill="var(--teal-light)"/>
    <polygon points="290,500 322,530 290,560" fill="var(--teal)" opacity="0.85"/>
    <polygon points="322,490 410,490 322,575" fill="var(--teal)" opacity="0.85"/>
    <polygon points="765,713 839,713 839,645" fill="var(--teal-light)" opacity="0.9"/>
    <polygon points="0,700 95,740 0,780" fill="var(--teal)"/>
    <polygon points="360,740 460,740 460,830" fill="var(--teal)" opacity="0.85"/>
    <polygon points="400,937 460,880 460,937" fill="var(--teal-light)" opacity="0.9"/>
    <polygon points="600,978 630,960 630,996" fill="var(--teal)"/>
    <polygon points="641,978 671,960 671,996" fill="var(--teal)"/>
    <polygon points="682,978 712,960 712,996" fill="var(--teal-light)"/>
    <polygon points="760,50 820,50 820,110" fill="var(--teal-pale)"/>
  </svg>

  <div class="headline-bar headline-bar--first">Interested in doing<strong>something</strong></div>
  <div class="headline-bar headline-bar--second"><strong>Different</strong>next year?</div>

  <p class="match"><span class="big">Norway +</span><span class="small">Folk High School</span><span class="small">= A good match</span></p>

  <p class="feature feature--language">Learn the Norwegian<br>language and culture</p>
  <p class="feature feature--living">Live close,<br>socialize<br>and be a part<br>of a Norwegian<br>boarding school</p>
  <p class="feature feature--location">Idyllically located in<br>beautifully natural<br>surroundings in a small<br>town south of Norway</p>

  <div class="closing"><strong>Take a chance,</strong> this could easily<br>be a <strong>perfect year</strong> for you!</div>

  <div class="contact">
    <span class="web">www.fhvbrekka.no</span>
    <span class="email">post@fhvbrekka.no</span>
    <span class="phone">+47 52 64 90 37</span>
  </div>

  <div class="school-mark">
    <span class="square"></span>
    <span class="name">Folkehøgskolen Vestbrekka</span>
  </div>

</div>
</body>
</html>
```